Business Card Design for Varomir Facility Services

We are looking for a Business Card Design for the Company "Varomir Facility Services."
Front side:
- Company Logo (small)
- Company Name, address, pohone, website and personal data.
- white background, for text e.g. company colors (blue or green like in the logo)
Please use following data:
Company data:
Varomir Facility Services Kostelac
Birkenhaldweg 14
6342 Lindenau
www.varomir-fs.ch
Person data:
Tarik Kostelac
Geschäftsführer
+41 76 519 47 83
info@varomir-fs.ch
Back side:
could be colored in blue or green
please use a big logo sing and some smaller icons to say what is all beeing offered in facility services, like cleaning, maintenance cleaning
industrial cleaning, caretaking, gardening, disposal. There is no need for everyone of the icons if there are similar or an icon is standing for more of them.
colors to use:
blue: HEX 246BB0
green: HEX 52B33E

```html
<!DOCTYPE html>
<html lang="de">
<head>
<meta charset="utf-8">
<title>Varomir Facility Services – Visitenkarte</title>
<link href="https://fonts.googleapis.com/css2?family=Montserrat:wght@400;500;600;700&display=swap" rel="stylesheet">
<style>
  :root {
    --brand-blue: #246BB0;
    --brand-blue-light: #3A83C9;
    --brand-green: #52B33E;
    --card-dark: #1b1b1d;
    --card-dark-map: #2a2a2d;
    --paper: #ffffff;
    --stage: #e9e7e4;
    --text-light: #ffffff;
  }
  * { box-sizing: border-box; margin: 0; padding: 0; }
  html, body { width: 1200px; height: 716px; overflow: hidden; }
  body {
    background: var(--stage);
    font-family: "Montserrat", Arial, sans-serif;
    position: relative;
  }
  .card {
    position: absolute;
    top: 208px;
    width: 520px;
    height: 300px;
    border-radius: 4px;
    overflow: hidden;
    box-shadow: 0 10px 26px rgba(0,0,0,.18);
  }
  /* back side */
  .card-back { left: 50px; background: var(--card-dark); }
  .world-map {
    position: absolute;
    left: 40px; top: 30px;
    width: 440px; height: 240px;
    border-radius: 40% 45% 38% 50%;
    background: radial-gradient(ellipse at center, var(--card-dark-map) 0%, var(--card-dark) 75%);
  }
  .back-brand {
    position: absolute;
    left: 0; right: 0; top: 118px;
    display: flex; align-items: center; justify-content: center; gap: 12px;
  }
  .brand-dot {
    width: 22px; height: 22px; border-radius: 50%;
    background: var(--brand-green);
    flex: none;
  }
  .back-brand .brand-name {
    color: var(--brand-blue-light);
    font-weight: 600;
    font-size: 30px;
    letter-spacing: .5px;
  }
  /* front side */
  .card-front { left: 630px; background: var(--brand-blue); }
  .front-shape { position: absolute; inset: 0; }
  .contact {
    position: absolute;
    left: 28px; top: 34px;
    color: var(--text-light);
    font-size: 14px;
    line-height: 1.35;
  }
  .contact .person-name { font-weight: 700; font-size: 19px; }
  .contact .person-role { font-size: 14px; margin-bottom: 12px; }
  .contact .address { margin-bottom: 10px; font-size: 15px; }
  .contact-line { display: flex; align-items: center; gap: 7px; font-size: 14px; }
  .contact-line svg { width: 11px; height: 11px; flex: none; }
  .contact-line .web-strong { font-weight: 600; }
  .front-brand {
    position: absolute;
    left: 262px; top: 128px; width: 240px;
    display: flex; align-items: center; gap: 10px;
  }
  .front-brand .brand-name {
    color: var(--brand-blue);
    font-weight: 600;
    font-size: 21px;
    line-height: 1.15;
  }
</style>
</head>
<body>

  <section class="card card-back" aria-label="Rückseite der Visitenkarte">
    <div class="world-map" role="img" aria-label="Dezente Weltkarte als Hintergrund"></div>
    <div class="back-brand">
      <span class="brand-dot"></span>
      <span class="brand-name">Varomir Facility Services</span>
    </div>
  </section>

  <section class="card card-front" aria-label="Vorderseite der Visitenkarte">
    <svg class="front-shape" viewBox="0 0 520 300" width="520" height="300" aria-hidden="true">
      <circle cx="420" cy="215" r="215" fill="var(--paper)" stroke="var(--brand-green)" stroke-width="4"/>
    </svg>

    <div class="contact">
      <p class="person-name">Tarik Kostelac</p>
      <p class="person-role">Geschäftsführer</p>
      <p class="address">Birkenhaldweg 14<br>6342 Lindenau</p>
      <p class="contact-line">
        <svg viewBox="0 0 12 12" aria-hidden="true"><path d="M2.5 1h2l1 3-1.3 1a6 6 0 0 0 2.8 2.8L8 6.5l3 1v2a1.5 1.5 0 0 1-1.5 1.5A8.5 8.5 0 0 1 1 2.5 1.5 1.5 0 0 1 2.5 1z" fill="#fff"/></svg>
        +41 76 519 47 83
      </p>
      <p class="contact-line">
        <svg viewBox="0 0 12 12" aria-hidden="true"><rect x="1" y="2.5" width="10" height="7" fill="none" stroke="#fff" stroke-width="1.2"/><path d="M1 2.5l5 4 5-4" fill="none" stroke="#fff" stroke-width="1.2"/></svg>
        info@varomir-fs.ch
      </p>
      <p class="contact-line">
        <svg viewBox="0 0 12 12" aria-hidden="true"><circle cx="6" cy="6" r="4.8" fill="none" stroke="#fff" stroke-width="1.1"/><ellipse cx="6" cy="6" rx="2" ry="4.8" fill="none" stroke="#fff" stroke-width="1"/><path d="M1.2 6h9.6" stroke="#fff" stroke-width="1"/></svg>
        <span>www.<span class="web-strong">varomir-fs</span>.ch</span>
      </p>
    </div>

    <div class="front-brand">
      <span class="brand-dot"></span>
      <span class="brand-name">Varomir<br>Facility Services</span>
    </div>
  </section>

</body>
</html>
```